Spanish Student Needs a Cover for his PhD Dissertation

Hi everyone :) So, I'm a Corneal surgeon currently finishing my PhD, with a dissertation focused on the evaluation of quality of life in patients affected by a disease called Keratoconus. Just so you know, Keratoconus is a condition in which the cornea (the frontal part of the way) gets thin and bulgy and it decreases vision. What I did during my PhD was designing a questionnaire for evaluating quality of life in this kind of patients.
I need to design a hard cover for my dissertation, which is 200 sheets long. I like kind of minimalistic and geometric designs but I am totally open to suggestions. What needs to be in the cover is the name of the dissertation "Diseño, desarrollo y validación de una encuesta para evaluar el compromiso visual y emocional subjetivos en pacientes con Queratocono" and my name, "Iker Zurmendi". The other thing that needs to go there is the logo of my university (Universidad de Montehierro). Aside from that, anything else is up to the designer. It would be important to use the kind of "red" color I am using in the dissertation. I am attaching the frontal page of my dissertation so you know what kind of design and colors I am using.
In the back part, of the cover, there should be this small inscription: "Iker Zurmendi, MD, es un Oftalmólogo Subespecialista en Cirugía Refractiva de la Universidad Tecnológica Cordillerana (Colombia) y la Universidad de Montehierro (España). Actualmente se desempeña como miembro del Departamento de Córnea y Cirugía Refractiva de la Clínica de Oftalmología Miraluz y como director de su propia compañía de emprendimiento médico Silver Heron Surgical". Please leave a space to place my picture; I will have it taken this week so I don't have it right now, you can just leave the blank spot and I will include it later
The size of the pages is standard "letter" size.
Thanks a lot!

Target Market(s)

PhD Scholars

Font styles to use
Serif

Requirements
Must have
• The "red" color I use on my font. It must be formal but "young".
Nice to have
• I like to keep the design clean, kind of "formal with a young" touch so to speak. I really like gray colors, so it would be nice to have broad areas of gray. I love geometrical designs.
I have uploaded a very early version a friend of mine made (it even had a different title); this can be a starting point for you to work on, but I am more than open to suggestions and new ideas.
Should not have
• Please don't use my whole name, Iker Zurmendi is fine. I don't like ALL CAPITALS.

```html
<!DOCTYPE html>
<html lang="es">
<head>
<meta charset="utf-8">
<title>Queratocono – Cubierta de tesis</title>
<link href="https://fonts.googleapis.com/css2?family=Noto+Serif:wght@400;700&family=Poppins:wght@700&display=swap" rel="stylesheet">
<style>
  :root {
    --ink: #262626;
    --wine: #8b1c35;
    --crimson: #b01e42;
    --deep-red: #1e0409;
    --band-gray: #c0c0c0;
    --soft-gray: #adb1b9;
    --paper: #ffffff;
    --label: #a3173a;
  }
  * { margin: 0; padding: 0; box-sizing: border-box; }
  html, body { width: 1200px; height: 831px; overflow: hidden; background: var(--paper); }
  body { position: relative; font-family: "Noto Serif", serif; }

  .side-label {
    position: absolute;
    font-family: "Noto Serif", serif;
    font-size: 21px;
    color: var(--label);
    transform: translateX(-50%);
  }
  .side-label--front { left: 314px; top: 52px; }
  .side-label--back { left: 888px; top: 59px; }

  .cover {
    position: absolute;
    top: 120px;
    width: 473px;
    height: 612px;
    background: var(--ink);
    overflow: hidden;
    box-shadow: 12px 12px 8px rgba(0,0,0,0.85);
  }
  .cover--front { left: 72px; }
  .cover--back { left: 642px; }
  .cover-art { position: absolute; inset: 0; }

  .thesis-title {
    position: absolute;
    left: 26px;
    top: 52px;
    width: 320px;
    color: #fff;
    font-weight: 700;
    font-size: 19px;
    line-height: 24.6px;
    letter-spacing: 0.05em;
  }

  .university {
    position: absolute;
    left: 338px;
    top: 6px;
    width: 120px;
    text-align: center;
    color: #fff;
  }
  .university-seal {
    width: 44px; height: 44px;
    margin: 0 auto;
    border-radius: 50%;
    background: #f3efe9;
  }
  .university-rule {
    height: 1px;
    margin: 8px 0 4px;
    background: rgba(255,255,255,0.55);
  }
  .university-name {
    font-size: 8.6px;
    font-weight: 700;
    white-space: nowrap;
  }
  .doctoral-badge {
    width: 119px; height: 26px;
    margin-top: 6px;
    background: #fff;
  }

  .author-name {
    position: absolute;
    left: 22px;
    top: 563px;
    font-family: "Poppins", sans-serif;
    font-weight: 700;
    font-size: 20px;
    letter-spacing: 0.09em;
    color: #111;
  }

  .author-bio {
    position: absolute;
    left: 0; right: 0;
    top: 33px;
    text-align: center;
    color: #fff;
    font-size: 13.2px;
    line-height: 16.7px;
  }
  .photo-slot {
    position: absolute;
    left: 0; right: 0;
    top: 366px;
    text-align: center;
    color: #fff;
    font-size: 13.2px;
  }
</style>
</head>
<body>
  <div class="side-label side-label--front">Front</div>
  <div class="side-label side-label--back">Back</div>

  <section class="cover cover--front">
    <svg class="cover-art" width="473" height="612" viewBox="0 0 473 612">
      <defs>
        <clipPath id="upper"><rect x="0" y="0" width="473" height="440"/></clipPath>
        <clipPath id="lower"><rect x="0" y="440" width="473" height="172"/></clipPath>
        <linearGradient id="eye-tones" x1="0" y1="0" x2="1" y2="1">
          <stop offset="0" stop-color="#b9876a"/>
          <stop offset="0.45" stop-color="#8a4a22"/>
          <stop offset="0.7" stop-color="#c07c2a"/>
          <stop offset="1" stop-color="#d9d6d3"/>
        </linearGradient>
      </defs>
      <circle cx="480" cy="-10" r="180" fill="var(--wine)"/>
      <rect x="0" y="440" width="473" height="172" fill="var(--band-gray)"/>
      <circle cx="217" cy="375" r="190" fill="#2c2c2c" clip-path="url(#upper)"/>
      <circle cx="217" cy="375" r="190" fill="var(--soft-gray)" clip-path="url(#lower)"/>
      <circle cx="409" cy="413" r="253" fill="var(--wine)"/>
      <circle cx="409" cy="413" r="253" fill="var(--deep-red)" clip-path="url(#upper)" opacity="0.9"/>
      <polygon role="img" aria-label="Fotografía en primer plano de un ojo de iris ámbar con pestañas"
        points="168,444 420,188 473,241 473,612 370,612" fill="url(#eye-tones)"/>
      <polygon points="150,325 250,228 350,325 250,422" fill="#a87860" opacity="0.85"/>
      <polygon points="305,195 420,85 473,140 473,230 420,282" fill="#c08f7a" opacity="0.85"/>
      <polygon points="223,333 302,254 381,333 302,412" fill="#ffffff" opacity="0.15"/>
      <polygon points="133,566 170,529 207,566 170,603" fill="#ffffff" opacity="0.3"/>
      <polygon points="243,566 282,527 321,566 282,605" fill="#ffffff" opacity="0.25"/>
      <polygon points="354,545 420,480 473,533 473,612 420,612" fill="#ffffff" opacity="0.3"/>
    </svg>

    <h1 class="thesis-title">"Diseño, desarrollo y validación de una encuesta para evaluar el compromiso visual y emocional subjetivos en pacientes con Queratocono"</h1>

    <div class="university">
      <div class="university-seal"></div>
      <div class="university-rule"></div>
      <div class="university-name">Universidad de Montehierro</div>
      <div class="doctoral-badge"></div>
    </div>

    <p class="author-name">Iker Zurmendi</p>
  </section>

  <section class="cover cover--back">
    <svg class="cover-art" width="474" height="612" viewBox="0 0 474 612">
      <circle cx="-59" cy="387" r="186" fill="var(--crimson)"/>
      <circle cx="-59" cy="387" r="86" fill="var(--ink)"/>
      <circle cx="533" cy="387" r="190" fill="var(--crimson)"/>
      <circle cx="533" cy="387" r="89" fill="var(--ink)"/>
    </svg>

    <p class="author-bio">"Iker Zurmendi, MD, es un Oftalmólogo<br>
      Subespecialista en Cirugía Refractiva de la<br>
      Universidad Tecnológica Cordillerana<br>
      (Colombia) y la Universidad de Montehierro<br>
      (España). Actualmente se desempeña como<br>
      miembro del Departamento de Córnea y<br>
      Cirugía Refractiva de la Clínica de<br>
      Oftalmología Miraluz y como director de<br>
      su propia compañía de emprendimiento<br>
      médico Silver Heron Surgical"</p>

    <p class="photo-slot">Author Photo here</p>
  </section>
</body>
</html>
```